Business card design Needed for new logo / Construction business, home extensions and new builds

We need a business card design using our new logo files which i will attach to this project :)

We are a small construction business specialising in home extensions, new builds and property development. We are very ambitious and would appreciate professional and elegant designs for our new business card.

Very serious about using the services on MakerQuarry and recently acquired our new logo from here :)

Please get involved, i will feedback when i can as i am very busy but can respond daily, thanks

Target Market(s)

People that want to build onto their houses, new building developments or adding too their existing property

Industry/Entity Type

Construction

Contact Information for Business Card

Renwick Tolliver Construction, Lionel Ashby (Managing Director), Tel 07822254961, email - info@renwick-tolliver, www.renwick-tolliver.co.uk

Colors

Designer to choose colors to be used in the design.

Requirements
Must have
• I like a deep grey on the back please. A lot of you have provided black from and back, try mixing things up a little. The black looks cool 😎 Thanks

```html
<!DOCTYPE html>
<html lang="en">
<head>
<meta charset="utf-8">
<title>Renwick Tolliver Construction – Business Card</title>
<link href="https://fonts.googleapis.com/css2?family=Arimo:wght@400;700&display=swap" rel="stylesheet">
<style>
  :root {
    --backdrop: #e9e7e3;
    --gold-light: #ecc983;
    --gold-mid: #d2a24e;
    --gold-deep: #a8741f;
    --charcoal: #333335;
    --ink: #141414;
    --white: #f2f2f2;
    --silver-light: #e4e4e6;
    --silver-dark: #9a9a9e;
    --divider: #5a5a5c;
  }
  * { box-sizing: border-box; margin: 0; padding: 0; }
  html, body {
    width: 1200px; height: 912px; overflow: hidden;
    background: var(--backdrop);
    font-family: "Arimo", Arial, sans-serif;
  }
  .canvas { position: relative; width: 1200px; height: 912px; }

  .card {
    position: absolute; width: 600px; height: 343px;
    box-shadow: 0 10px 28px rgba(0,0,0,.25);
    overflow: hidden;
  }

  /* Front */
  .card-front {
    left: 60px; top: 70px;
    background: radial-gradient(ellipse at 42% 30%, var(--gold-light) 0%, var(--gold-mid) 45%, var(--gold-deep) 100%);
  }
  .front-brand {
    position: absolute; left: 0; right: 0; top: 120px;
    display: flex; align-items: center; justify-content: center; gap: 12px;
    color: var(--ink); font-weight: 700; font-size: 26px; letter-spacing: .5px;
  }
  .brand-square { width: 16px; height: 16px; background: currentColor; }
  .front-web {
    position: absolute; left: 0; right: 0; bottom: 62px; text-align: center;
    color: var(--ink); font-size: 15px; letter-spacing: 3.5px;
  }

  /* Back */
  .card-back { left: 540px; top: 470px; background: var(--charcoal); }
  .back-brand {
    position: absolute; left: 34px; top: 150px; width: 240px;
    display: flex; align-items: center; gap: 10px;
    color: var(--gold-mid); font-weight: 700; font-size: 17px; line-height: 1.25;
  }
  .back-brand .brand-square { flex: none; width: 12px; height: 12px; }
  .divider {
    position: absolute; left: 290px; top: 40px; width: 1px; height: 200px;
    background: var(--divider);
  }
  .person { position: absolute; left: 318px; top: 58px; }
  .person-name { color: var(--gold-mid); font-weight: 700; font-size: 25px; }
  .person-role { color: var(--white); font-size: 15px; margin-top: 4px; }
  .contacts { position: absolute; left: 318px; top: 140px; list-style: none; }
  .contacts li {
    display: flex; align-items: center; gap: 9px;
    color: var(--white); font-size: 15px; margin-bottom: 7px;
  }
  .contacts svg { width: 14px; height: 14px; flex: none; fill: var(--gold-mid); }

  .band-gold {
    position: absolute; left: 0; bottom: 0; width: 78%; height: 28px;
    background: linear-gradient(90deg, var(--gold-deep), var(--gold-light) 55%, var(--gold-mid));
  }
  .band-silver {
    position: absolute; right: 0; bottom: 28px; width: 22%; height: 22px;
    background: linear-gradient(90deg, var(--silver-dark), var(--silver-light) 60%, var(--silver-dark));
  }
</style>
</head>
<body>
<main class="canvas">

  <section class="card card-front">
    <div class="front-brand"><span class="brand-square"></span>Renwick Tolliver Construction</div>
    <p class="front-web">www.renwick-tolliver.co.uk</p>
  </section>

  <section class="card card-back">
    <div class="back-brand"><span class="brand-square"></span>Renwick Tolliver Construction</div>
    <div class="divider"></div>

    <div class="person">
      <p class="person-name">Lionel Ashby</p>
      <p class="person-role">Managing Director</p>
    </div>

    <ul class="contacts">
      <li>
        <svg viewBox="0 0 24 24" aria-hidden="true"><path d="M6.6 10.8a15.1 15.1 0 0 0 6.6 6.6l2.2-2.2c.3-.3.7-.4 1-.2 1.1.4 2.3.6 3.6.6.6 0 1 .4 1 1V20c0 .6-.4 1-1 1A17 17 0 0 1 3 4c0-.6.4-1 1-1h3.5c.6 0 1 .4 1 1 0 1.3.2 2.5.6 3.6.1.3 0 .7-.2 1z"/></svg>
        07822254961
      </li>
      <li>
        <svg viewBox="0 0 24 24" aria-hidden="true"><path d="M2 5h20v14H2z M3.5 6.5 12 13l8.5-6.5" fill="none" stroke="#d2a24e" stroke-width="2"/></svg>
        info@renwick-tolliver
      </li>
      <li>
        <svg viewBox="0 0 24 24" aria-hidden="true"><circle cx="12" cy="12" r="9" fill="none" stroke="#d2a24e" stroke-width="2"/><path d="M3 12h18M12 3c3 3 3 15 0 18M12 3c-3 3-3 15 0 18" fill="none" stroke="#d2a24e" stroke-width="1.6"/></svg>
        www.renwick-tolliver.co.uk
      </li>
    </ul>

    <div class="band-silver"></div>
    <div class="band-gold"></div>
  </section>

</main>
</body>
</html>
```